Doctors Office Web Design

Name of the business is Lian-Hua Qiu M.D.
We need a web design that is attractive for women that want to see Dr. Lian-Hua Qiu for Obstetrician Gynecology and Pregnancy care. Dr. Qiu earned her degree from Harwell Ridge Medical College of obstetrician gynecology. We want to attract women of child bearing ages to come to our offices for health, education, and pregnancies.

Please visit http://www.drqiucareweb.example/ to help you get a feel for who we are. We will be adding some pictures and logo in the next few days.

We are looking for to have pages for and tabs including
About Us- History, Our Staff, Dr. Qiu
Patient Information- Appointments, E-Prescriptions, Payments Accepted, Insurance
Health- General, Sexual, Mental, Affiliates
Pregnancy- Minimally invasive surgery(our specialty), 4-D Ultra Sound, Hospital Affiliations
Media- News,Pictures, Videos
Locations- Palmetto Office, Larkfield Office

The colors we would like to use are pastel colors, magenta, and plum

Target Market(s)

Women of all ages with an emphasis on 25-65 year olds

Industry/Entity Type

Business

Requirements
Must have
• Needs to include a location for a our videos and pictures that I will submit shortly. We also want a map to our location or atleast a place for one.
Nice to have
• A place for a google map of our office locations.

```html
<!DOCTYPE html>
<html lang="en">
<head>
<meta charset="utf-8">
<title>Lian-Hua Qiu M.D.</title>
<link rel="stylesheet" href="https://fonts.googleapis.com/css2?family=Roboto+Condensed:wght@300&family=Open+Sans:wght@400;600&family=Arimo&display=swap">
<style>
:root{
  --pink-top:#f7b3cb;
  --pink-bottom:#f87fa9;
  --magenta-top:#ee86ad;
  --magenta-bottom:#c8235a;
  --cream:#fcf0e3;
  --tan:#c9a287;
  --heading:#8c7361;
  --body:#927c68;
  --white:#ffffff;
}
*{margin:0;padding:0;box-sizing:border-box}
html,body{width:1200px;height:1027px;overflow:hidden}
body{position:relative;background:var(--cream);font-family:"Open Sans",sans-serif;color:var(--body)}
.top-band{position:absolute;left:0;top:0;width:1200px;height:105px;background:linear-gradient(var(--pink-top),var(--pink-bottom))}
.office{position:absolute;top:10px;color:var(--white);font-style:normal;font-size:12.5px;line-height:16px;letter-spacing:.4px}
.office-larkfield{right:842px;text-align:right}
.office-palmetto{left:842px}
.title-box{position:absolute;left:370px;top:0;width:460px;height:126px;background:linear-gradient(var(--magenta-top),var(--magenta-bottom));box-shadow:0 2px 4px rgba(0,0,0,.35);display:flex;align-items:center;justify-content:center}
.site-title{font-family:"Roboto Condensed",sans-serif;font-weight:300;font-size:56px;letter-spacing:-2.5px;color:var(--white);text-shadow:1px 2px 2px rgba(90,20,50,.45);margin-top:-12px}
.hero{position:absolute;left:0;top:105px;width:1200px;height:308px;background:var(--white)}
.portrait{position:absolute;left:420px;top:126px;width:410px;height:287px;background:linear-gradient(160deg,#6b5e58,#d9c6c4 45%,#f4f2f5 70%,#2a2a30)}
.nav-shadow{position:absolute;left:0;top:413px}
.nav{position:absolute;left:230px;top:413px;width:740px;height:44px;background:var(--tan);display:flex;justify-content:center;align-items:center;gap:11px;color:var(--white);font-family:"Arimo",sans-serif;font-size:14.5px;list-style:none}
.content{position:absolute;left:100px;top:490px;width:656px}
h2{font-family:"Arimo",sans-serif;font-weight:400;font-size:24px;color:var(--heading);margin-bottom:8px;padding-left:1px}
.content p{font-size:12.3px;line-height:20px;text-align:justify;letter-spacing:.55px;word-spacing:.5px;hyphens:auto;-webkit-hyphens:auto;margin-bottom:20px}
.divider{position:absolute;left:776px;top:497px}
.insurance{position:absolute;left:816px;top:490px}
.insurance ul{list-style:none;margin-top:12px;padding-left:2px}
.insurance li{font-size:12.3px;line-height:17.9px;letter-spacing:.4px}
</style>
</head>
<body>
<header>
  <div class="top-band"></div>
  <address class="office office-larkfield">4820 Seagrape Avenue Suite<br>204-205<br>Larkfield, Florida&nbsp; 33900<br>Tel:&nbsp; (555) 210-7391<br>Fax: (555) 210-7392</address>
  <address class="office office-palmetto">2275 N.W. 9th Street<br>Suite 3B<br>Palmetto, Florida&nbsp; 33911<br>Tel:&nbsp; (555) 318-6604<br>Fax:&nbsp; (555) 318-6605</address>
  <div class="hero"></div>
  <div class="portrait" role="img" aria-label="Portrait photo of Dr. Qiu in a white coat seated in a black office chair"></div>
  <div class="title-box"><h1 class="site-title">Lian-Hua Qiu M.D</h1></div>
</header>
<svg class="nav-shadow" width="1200" height="20" aria-hidden="true">
  <defs><linearGradient id="navShade" x1="0" y1="0" x2="0" y2="1"><stop offset="0" stop-color="#8a8079" stop-opacity=".75"/><stop offset="1" stop-color="#8a8079" stop-opacity="0"/></linearGradient></defs>
  <path d="M100 0 H1100 Q1000 4 900 16 H300 Q200 4 100 0Z" fill="url(#navShade)"/>
</svg>
<ul class="nav">
  <li>HOME</li><li>|</li><li>ABOUT US</li><li>|</li><li>PATIENT INFORMATION</li><li>|</li><li>HEALTH</li><li>|</li><li>PREGNANCY</li><li>|</li><li>MEDIA</li><li>|</li><li>LOCATIONS</li>
</ul>
<main class="content">
  <h2>About Us</h2>
  <p>Lorem ipsum dolor sit amet, consectetur adipiscing elit. Ut sit amet nibh leo, quis tincidunt neque. Suspendisse eleifend justo in leo placerat accumsan vitae at augue. Cras condimentum elementum malesuada. Aliquam vel imperdiet odio. Cras vel luctus ante. Vestibulum pellentesque, lacus ac accumsan ullamcorper, odio turpis ornare justo, vel tempor nulla urna sit amet sem. Quisque adipiscing imperdiet sapien at dapibus. Mauris suscipit augue vitae metus accumsan a cursus lectus porta. Nullam fringilla consectetur velit, nec feugiat felis pharetra.</p>
  <p>Ut magna massa, blandit eget porttitor non, congue sit amet justo. Nunc ac mi lacus. Donec dapibus justo vitae ante porta consequat. Proin dui diam, fermentum vitae consectetur vel, elementum nec ipsum. Duis sed erat vel nisl sollicitudin porttitor. Sed volutpat pharetra dui. Phasellus malesuada gravida magna sed semper.</p>
  <p>Pellentesque eros turpis, congue quis consectetur sit amet, varius sed dui. Donec id orci elit. Ut fermentum odio vitae nisi hendrerit laoreet. Curabitur orci metus, feugiat id tincidunt sodales, aliquet sit amet risus. Nulla facilisi. Aenean vehicula est vitae velit accumsan mollis.</p>
  <p>Proin nec velit lectus, non bibendum metus. Vestibulum fringilla eros sed metus interdum mollis. Nunc vitae justo eu metus ullamcorper posuere eget ut neque. Integer in ultricies arcu. Sed cursus, ipsum at imperdiet aliquam, tortor turpis tempor dui, porta elementum eros massa ut augue. Morbi et augue at nulla consequat porta eget eget velit.</p>
  <p>Donec tempus diam ac dolor facilisis rhoncus id nec lacus. Aenean sem nisl, dignissim ut pellentesque at, porttitor vel nulla. Nulla pellentesque venenatis malesuada.</p>
</main>
<svg class="divider" width="14" height="515" aria-hidden="true">
  <defs><linearGradient id="divShade" x1="0" y1="0" x2="1" y2="0"><stop offset="0" stop-color="#7d726b" stop-opacity=".7"/><stop offset="1" stop-color="#7d726b" stop-opacity="0"/></linearGradient></defs>
  <path d="M4 0 Q14 257 4 515 Q2 257 4 0Z" fill="url(#divShade)"/>
</svg>
<aside class="insurance">
  <h2>Insurance Plans</h2>
  <ul>
    <li>Lanterra (All Products)</li><li>Brightwell Heritage</li><li>Brightwell Medical Security</li><li>Ferncliff/ Tallow Care PPO Network</li><li>Harrowgate Shield Plan</li><li>QPN/Clearspring/Health Adv</li><li>Velmora</li><li>Tessaly PPO</li><li>Orvanne HealthCare</li><li>Kindlewood Health</li><li>Quillbrook Health</li><li>Saltmarsh Health Choice</li><li>Brambleton PPO Network</li><li>Thistledown Options</li><li>Marrowind Health</li><li>Healthy Driftwood Shores</li><li>Calvento PPO &amp; EPO</li><li>Senior Harbor Plan</li><li>Ostrovane</li><li>Pellwick PPO Network</li><li>Greyfen Source PPO</li><li>Wrenfield County Healthcare District</li><li>Ashcombe Health Plans</li><li>Dovecote Health</li><li>Corrandel Healthcare Systems</li><li>Fennimore HealthCare</li><li>Linwood Vale HMO</li>
  </ul>
</aside>
</body>
</html>
```